House flipping business web site needed

pinecrestholdingsgroup.example.
I am a residential developer in Northern NJ and I am looking for a fresh new updated website. I have an intro video about my company being made now. I don't update it very often but I want an easy format that I can add update photos to on projects I have worked on or homes I renovate for sale.

Target Market(s)

investors into my projects so a portfolio , people looking to sell their homes to me.

Industry/Entity Type

Real Estate Development

Number of Pages Required

4 page

Font styles to use
Serif

Colors
33b8a4
39a9d7
cadf82

Requirements
Must have
• space for an intro video about my company
• a portfolio with pictures and information about each project
• Markets we serve- Morris County, NJ
• My logo- already created
• SEO
• Yes I would like this to function over all platforms. Phone, computer, all platforms.
• history and background page
• I am looking for a completed page that I can upload to the site that hosts my website
Nice to have
• I want something creative, easy to navigate. modern.

```html
<!DOCTYPE html>
<html lang="en">
<head>
<meta charset="utf-8">
<title>Pinecrest Holdings Group — House Flipping in New Jersey</title>
<link href="https://fonts.googleapis.com/css2?family=Oswald:wght@500&family=Roboto:wght@400;500&display=swap" rel="stylesheet">
<style>
:root{
  --teal:#33b8a4;
  --blue:#39a9d7;
  --blue-deep:#2a93c4;
  --ink:#222;
  --text:#555;
  --light:#f4f5f6;
  --footer:#2b2b2b;
  --footer-bottom:#1f1f1f;
  --muted:#c9c9c9;
}
*{box-sizing:border-box;margin:0;padding:0}
html,body{width:1200px;height:2663px;overflow:hidden}
body{position:relative;font-family:"Roboto",Arial,sans-serif;color:var(--text);background:#fff}
.abs{position:absolute}

/* header */
.topline{left:0;top:0;width:1200px;height:5px;background:var(--blue)}
.header{left:0;top:5px;width:1200px;height:93px;background:var(--light);z-index:2}
.brand{left:88px;top:-20px;width:154px;height:158px;border-radius:50%;background:var(--light);z-index:3;display:flex;align-items:center;justify-content:center;text-align:center}
.brand span{font:500 15px/1.25 "Roboto",sans-serif;color:var(--blue-deep);letter-spacing:.5px;padding:0 14px}
.nav a{position:absolute;top:30px;height:41px;line-height:41px;font-size:16px;color:#333;text-decoration:none;z-index:3}
.nav .active{background:var(--teal);color:#fff;padding:0 17px;left:390px}

/* hero */
.hero{left:0;top:98px;width:1200px;height:555px;background:linear-gradient(160deg,#3f5a2a 0%,#6d7d5c 35%,#9aa59a 50%,#4c6b2c 75%,#2f4a1c 100%)}
.hero-caption{left:108px;top:412px;padding:14px 14px 12px;background:rgba(0,0,0,.35)}
.hero-caption h1{font:500 44px/1.1 "Oswald",sans-serif;color:#fff;letter-spacing:.5px;white-space:nowrap}
.hero-caption p{font:500 25px/1.3 "Oswald",sans-serif;color:#fff;margin-top:6px}
.slider-arrow{top:562px;width:36px;height:36px;border-radius:50%;background:#1c1c1c}

/* welcome */
.welcome-title{left:92px;top:743px;width:530px;font:400 23px/1.2 "Roboto",sans-serif;color:var(--ink);white-space:nowrap}
.welcome-title em{font-style:normal;color:var(--blue)}
.welcome-text{left:92px;top:788px;width:524px;font-size:13.5px;line-height:23.5px;color:var(--text)}
.btn{background:var(--teal);color:#fff;font-size:13px;text-align:center;border-radius:18px}
.read-more{left:92px;top:943px;width:116px;height:35px;line-height:35px}
.video-frame{left:639px;top:717px;width:472px;height:277px;border:1px solid #ddd;padding:5px;background:#fff;box-shadow:0 0 4px rgba(0,0,0,.12)}
.video-frame .still{width:100%;height:100%;background:linear-gradient(180deg,#5d7a86 0%,#7c8f6b 45%,#cfd3c8 60%,#5e7a3a 100%)}
.play{left:839px;top:821px}

/* projects */
.projects{left:0;top:1056px;width:1200px;height:458px;background:linear-gradient(135deg,#2f9fd0 0%,#3aaedb 45%,#2b8fc0 100%)}
.section-title{width:1200px;text-align:center;font:500 27px/1.2 "Roboto",sans-serif}
.project-card{top:1184px;width:246px;height:268px;background:#fff}
.project-card .photo{height:215px}
.project-card h3{height:53px;text-align:center;font:400 14.5px/53px "Roboto",sans-serif;color:#333;letter-spacing:.3px}

/* blog */
.blog-title{top:1576px;color:var(--ink);font-weight:400}
.blog-title em{font-style:normal;color:var(--blue)}
.post{top:1635px;width:316px}
.post .photo-frame{height:190px;border:1px solid #ddd;padding:4px;position:relative}
.post .photo{width:100%;height:100%}
.date{position:absolute;left:4px;top:52px;width:45px;text-align:center;color:#fff}
.date .day{background:var(--teal);height:45px;padding-top:5px;font-size:19px;line-height:22px}
.date .day small{display:block;font-size:10px;line-height:14px}
.date .year{background:#2b2b2b;height:42px;line-height:42px;font-size:14px}
.post h3{margin-top:20px;font:400 15px/1.2 "Roboto",sans-serif;color:#222}
.post p{margin-top:8px;font-size:12px;line-height:20px;color:#888}
.post .more{margin-top:6px;display:block;font-size:12.5px;color:var(--teal)}

/* map */
.map{left:0;top:1988px;width:1200px;height:350px;background:linear-gradient(120deg,#e4e4e4,#d8d8d8 50%,#e6e6e6)}
.map-card{left:135px;top:2116px;width:300px;height:138px;background:#fff;box-shadow:0 1px 5px rgba(0,0,0,.2);padding:14px 0 0 32px}
.map-card h4{font:400 15px/1.2 "Roboto",sans-serif;color:#222;margin-left:-1px}
.map-card li{list-style:none;display:flex;align-items:center;gap:10px;font-size:12px;color:#444;margin-top:11px;white-space:nowrap}

/* footer */
.footer{left:0;top:2338px;width:1200px;height:236px;background:var(--footer);color:#fff}
.footer h5{position:absolute;top:39px;font:400 17px/1.2 "Roboto",sans-serif;letter-spacing:.3px}
.footer .col{position:absolute;top:72px;font-size:12.5px;line-height:19px;color:#eee}
.email-field{margin-top:12px;width:216px;height:30px;background:#eee;color:#888;font-size:11.5px;padding:8px 8px}
.subscribe{margin-top:12px;width:95px;height:28px;line-height:28px;border-radius:2px;font-size:12px}
.tweet{display:flex;gap:8px;margin-bottom:14px}
.tweet em{font-style:italic}
.contact-line{display:block;white-space:nowrap}
.social{display:flex;align-items:center;gap:16px;margin-bottom:11px}
.social .ring{width:32px;height:32px;border:1px solid #eee;border-radius:50%}
.footer-bottom{left:0;top:2574px;width:1200px;height:89px;background:var(--footer-bottom);text-align:center;line-height:89px;font-size:12px;color:#fff}
</style>
</head>
<body>

<div class="abs topline"></div>
<header class="abs header">
  <nav class="nav">
    <a class="active" href="#">HOME</a>
    <a style="left:520px" href="#">ABOUT</a>
    <a style="left:639px" href="#">SERVICES</a>
    <a style="left:781px" href="#">PORTFOLIO</a>
    <a style="left:932px" href="#">BLOG</a>
    <a style="left:1038px" href="#">CONTACT</a>
  </nav>
</header>
<div class="abs brand"><span>PINECREST HOLDINGS GROUP</span></div>

<section class="abs hero" role="img" aria-label="Photo of a white cottage among tall trees with a green lawn"></section>
<div class="abs hero-caption">
  <h1>PINECREST HOLDINGS GROUP</h1>
  <p>HOUSE FLIPPING BUSINESS IN NEW JERSEY</p>
</div>
<svg class="abs slider-arrow" style="left:1031px" viewBox="0 0 36 36"><circle cx="18" cy="18" r="18" fill="#1c1c1c"/><path d="M20.5 11.5 14 18l6.5 6.5" fill="none" stroke="#fff" stroke-width="2.6"/></svg>
<svg class="abs slider-arrow" style="left:1075px" viewBox="0 0 36 36"><circle cx="18" cy="18" r="18" fill="#1c1c1c"/><path d="M15.5 11.5 22 18l-6.5 6.5" fill="none" stroke="#fff" stroke-width="2.6"/></svg>

<h2 class="abs welcome-title">WELCOME TO <em>PINECREST HOLDINGS GROUP</em></h2>
<p class="abs welcome-text">We are a team of experienced home buyers and renovators in the Morris County, NJ area. Our specialty is purchasing distressed homes and property. We then collaborate with the best talents in Northern New Jersey to renovate those properties and transform them into the best house in the neighborhood. As a result we create equity, a return on investment and most importantly we give home buyers a worry free property that provides a better way of life and hope for their future.</p>
<div class="abs btn read-more">READ MORE</div>
<div class="abs video-frame"><div class="still" role="img" aria-label="Intro video still of a white house with wooden steps under pine trees"></div></div>
<svg class="abs play" width="72" height="72" viewBox="0 0 72 72"><circle cx="36" cy="36" r="34" fill="rgba(40,40,40,.55)" stroke="#fff" stroke-width="3"/><path d="M29 22v28l22-14z" fill="#fff"/></svg>

<section class="abs projects" role="img" aria-label="Blue water texture background"></section>
<h2 class="abs section-title" style="top:1106px;color:#fff">OUR PROJECT</h2>
<div class="abs project-card" style="left:92px"><div class="photo" role="img" aria-label="Renovated open living room and kitchen" style="background:linear-gradient(180deg,#cfcac2,#6c6660 60%,#3a3330)"></div><h3>NEQUE PORRO QUISQUAM</h3></div>
<div class="abs project-card" style="left:348px"><div class="photo" role="img" aria-label="Renovated bathroom with window" style="background:linear-gradient(180deg,#c9c6b8,#a49e8a 55%,#6a5b48)"></div><h3>NEQUE PORRO QUISQUAM</h3></div>
<div class="abs project-card" style="left:605px"><div class="photo" role="img" aria-label="Staged bedroom with dark bedding" style="background:linear-gradient(180deg,#b9b5ab,#5a5550 55%,#2b2a2a)"></div><h3>NEQUE PORRO QUISQUAM</h3></div>
<div class="abs project-card" style="left:863px"><div class="photo" role="img" aria-label="Dining area with glass table" style="background:linear-gradient(180deg,#e2e0d8,#a5a39a 55%,#3d3a38)"></div><h3>NEQUE PORRO QUISQUAM</h3></div>

<h2 class="abs section-title blog-title">LATEST <em>BLOG</em></h2>
<article class="abs post" style="left:92px">
  <div class="photo-frame"><div class="photo" role="img" aria-label="House under construction with wood framing" style="background:linear-gradient(180deg,#c8c9c6,#9c7a58 50%,#6d5238)"></div>
    <div class="date"><div class="day">02<small>JUN</small></div><div class="year">2016</div></div></div>
  <h3>Neque porro quisquam</h3>
  <p>Lorem ipsum dolor sit amet, consectetur adipiscing elit. Sed blandit massa vel mauris sollicitudin dignissim.</p>
  <span class="more">Read More »</span>
</article>
<article class="abs post" style="left:444px">
  <div class="photo-frame"><div class="photo" role="img" aria-label="Renovated kitchen with dark cabinets" style="background:linear-gradient(180deg,#b8b2a6,#4a3a30 55%,#2a211d)"></div>
    <div class="date"><div class="day">02<small>JUN</small></div><div class="year">2016</div></div></div>
  <h3>Neque porro quisquam</h3>
  <p>Lorem ipsum dolor sit amet, consectetur adipiscing elit. Sed blandit massa vel mauris sollicitudin dignissim.</p>
  <span class="more">Read More »</span>
</article>
<article class="abs post" style="left:795px">
  <div class="photo-frame"><div class="photo" role="img" aria-label="Dark green house exterior with trees" style="background:linear-gradient(180deg,#9fb6c8,#3e4a3c 50%,#567a2e)"></div>
    <div class="date"><div class="day">02<small>JUN</small></div><div class="year">2016</div></div></div>
  <h3>Neque porro quisquam</h3>
  <p>Lorem ipsum dolor sit amet, consectetur adipiscing elit. Sed blandit massa vel mauris sollicitudin dignissim.</p>
  <span class="more">Read More »</span>
</article>

<section class="abs map" role="img" aria-label="Street map showing office locations"></section>
<div class="abs map-card">
  <h4>PINECREST HOLDINGS GROUP</h4>
  <ul>
    <li><svg width="10" height="10" viewBox="0 0 10 10"><path d="M2 0h2l1 3-1.5 1a6 6 0 0 0 2.5 2.5L7 5l3 1v2a2 2 0 0 1-2 2A8 8 0 0 1 0 2a2 2 0 0 1 2-2z" fill="var(--blue)"/></svg>1300 555 019</li>
    <li><svg width="11" height="9" viewBox="0 0 11 9"><rect width="11" height="9" fill="var(--blue)"/><path d="M0 0l5.5 5L11 0" fill="none" stroke="#fff"/></svg>info@pinecrestholdingsgroup.example</li>
    <li><svg width="9" height="12" viewBox="0 0 9 12"><path d="M4.5 0A4.5 4.5 0 0 0 0 4.5C0 8 4.5 12 4.5 12S9 8 9 4.5A4.5 4.5 0 0 0 4.5 0z" fill="var(--blue)"/><circle cx="4.5" cy="4.5" r="1.6" fill="#fff"/></svg>PO Box 512, Denville NJ 07834</li>
  </ul>
</div>

<footer class="abs footer">
  <h5 style="left:96px">NEWSLETTERS SIGN UP</h5>
  <div class="col" style="left:96px;width:230px">
    Sign up for our daily email by entering your information below
    <div class="email-field">Email address</div>
    <div class="btn subscribe">SUBSCRIBE</div>
  </div>

  <h5 style="left:394px">LATEST TWEET</h5>
  <div class="col" style="left:394px;top:78px;width:240px">
    <div class="tweet"><svg width="14" height="12" viewBox="0 0 14 12"><circle cx="7" cy="6" r="5" fill="#fff"/></svg><div>Featured Workspace : Northmill<br>nmill.example/q7Rb <em>10 hours ago</em></div></div>
    <div class="tweet"><svg width="14" height="12" viewBox="0 0 14 12"><circle cx="7" cy="6" r="5" fill="#fff"/></svg><div>Featured Workspace : Northmill<br>nmill.example/q7Rb <em>10 hours ago</em></div></div>
  </div>

  <h5 style="left:694px">GET IN TOUCH</h5>
  <div class="col" style="left:694px;top:78px;width:270px;line-height:20px;font-size:12px">
    <span class="contact-line">Address : 120 Birchwood Lane,</span>
    <span class="contact-line">Rockaway, NJ</span>
    <span class="contact-line" style="margin-top:12px">Phone : 201 555 0147</span>
    <span class="contact-line" style="margin-top:12px;font-size:11.5px">Email : info@pinecrestholdingsgroup.example</span>
  </div>

  <h5 style="left:973px">FOLLOW US ON</h5>
  <div class="col" style="left:973px;top:78px">
    <div class="social"><div class="ring"></div>Community</div>
    <div class="social"><div class="ring"></div>Updates</div>
    <div class="social"><div class="ring"></div>Gallery</div>
  </div>
</footer>
<div class="abs footer-bottom">Copyright © 2016. All Rights Reserved</div>

</body>
</html>
```